Home page design for Drone video business (the Business focusses on home videos for realtors)

Dear reader,

*I NEED DESIGNS OF ALL THE PAGES*
We need a first design of a homepage and of 4 other pages of the website of a business that sells drone video services. All the pages will need to be in the similar design style.
The video's are targeted at consumers that want to sell there home and would like to have a cool drone video of photos of their home.

How does the website look:
- has a navbar on top
- A cool looking banner of an areal drone.
- A Big header: with company name: SkyLoftReels
- A smaller subheader: We film your home to increase your chances of sale
- Then a section with a Big header: How does it work
- In this section a place for a vimeo explainitory video
- Then a similar navbar styled bar with a phone number and a email address
- Then a section where the videos porfolio is displayed in a cool way
- Inside this sectiona header: Our work

- A section with header: Why us?
- 4 symbols here with a subheader and some lorum ipsum text underneath (see wireframe images)

- Under that a: Contact us
- where you can put in name, email, phone, message box and a send button

- At the bottom a footer with phone number and a fake address for now.

Be creative. Use creative but serious color.
Use a serious font. Make it a sharp design. Sharp lines. Not to dark design and not to light design.

The wireframes are the same kind of images.
PLEASE PUT IN DESIGNS OF ALL THE PAGES

Good luck

Target Market(s)

People that want to sell home and want to make a cool drone video or photos of their home.

Industry/Entity Type

Business

Contact Information for Business Card

Lucas Wenning
lucas@skyloftreels.example
+31647208351

Logo Text

SkyLoftReels

Number of Pages Required

1 page

Font styles to use
Sans Serif

Requirements
Must have
• All the sections as explained in the instructions.
• The nav bar should have an about us, services, portfolio and a contact us buttons.
• See instruction for details.
• Must include designs of the front page, contact us, our services, portfolio and contact us.
• If you do add some designs for the "about us", "services", "prices", "portfolio" and "contact us" pages, you make a way better chance of winning the competition.
Nice to have
• designs for the other pages as described at the Must haves. You make a better chance of winning if you include them. Look at the wireframes to see the mockups for those pages. think creative about what kind of sections and design should be included in those pages.
Should not have
• bad designs.

```html
<!DOCTYPE html>
<html lang="en">
<head>
<meta charset="utf-8">
<title>SkyLoftReels – Home Drone Video</title>
<link rel="stylesheet" href="https://fonts.googleapis.com/css2?family=Lato:wght@400;700&family=Montserrat:wght@500;600;700&family=Open+Sans:wght@400;600&display=swap">
<style>
:root{
  --orange:#f15a29;
  --orange-dark:#c9441b;
  --ink:#1f1f1f;
  --text:#333333;
  --muted:#8a8a8a;
  --line:#d6d6d6;
  --bg-soft:#f2f2f2;
  --bg-why:#efefef;
  --bg-contact:#f7f7f7;
  --footer:#333333;
  --white:#ffffff;
}
*{box-sizing:border-box;margin:0;padding:0}
html,body{width:1200px;height:2338px;overflow:hidden}
body{font-family:'Lato',sans-serif;color:var(--text);background:var(--white);position:relative}

/* Header */
.site-header{position:relative;height:101px;border-top:4px solid var(--orange);background:var(--white)}
.brand{position:absolute;left:81px;top:30px;display:flex;align-items:center;gap:14px}
.brand-dot{width:30px;height:30px;border-radius:50%;background:var(--ink)}
.brand-name{font-family:'Montserrat',sans-serif;font-weight:700;font-size:30px;color:var(--orange);letter-spacing:.5px}
.header-phone{position:absolute;right:82px;top:16px;display:flex;align-items:center;gap:10px;font-size:19px;color:var(--ink)}
.header-phone svg{width:28px;height:28px}
.main-nav{position:absolute;right:82px;top:64px;display:flex;font-size:14px;color:var(--ink);letter-spacing:.3px}
.main-nav a{color:inherit;text-decoration:none;padding:0 29px;border-left:1px solid var(--line);line-height:18px;position:relative}
.main-nav a:first-child{border-left:none}
.main-nav a.is-active{color:var(--orange)}
.main-nav a.is-active::after{content:"";position:absolute;left:29px;right:29px;bottom:-7px;height:3px;background:var(--orange)}

/* Hero */
.hero{position:relative;height:480px;background:linear-gradient(180deg,#9dc0e6 0%,#b7cfe0 22%,#5f8a4a 40%,#8a6a5a 62%,#6d6f80 78%,#4f6f3c 100%)}
.hero-banner{position:absolute;left:203px;top:184px;width:817px;height:100px;background:rgba(20,20,20,.72);clip-path:polygon(6% 0,100% 0,94% 100%,0 100%);text-align:center;color:var(--white);font-family:'Montserrat',sans-serif;white-space:nowrap}
.hero-title{font-size:29px;font-weight:600;line-height:34px;margin-top:13px;letter-spacing:.3px}
.hero-sub{font-size:25px;font-weight:600;line-height:32px;margin-top:4px;letter-spacing:-.3px}

/* Section headings */
.section-title{font-family:'Open Sans',sans-serif;font-weight:400;font-size:31px;text-align:center;color:var(--ink);letter-spacing:.5px}
.section-title .accent{color:var(--orange)}
.divider{position:relative;width:486px;height:14px;margin:16px auto 0}
.divider::before{content:"";position:absolute;left:0;right:0;top:7px;height:1px;background:var(--line)}
.divider-dots{position:absolute;left:50%;top:0;transform:translateX(-50%);display:flex;gap:4px;background:inherit;padding:0 6px}
.divider-dots span{width:13px;height:13px;border-radius:50%;background:#c4c4c4}

/* How it works */
.how{height:513px;background:var(--bg-soft);padding-top:36px;position:relative}
.how .divider-dots{background:var(--bg-soft)}
.video-frame{position:absolute;left:280px;top:143px;width:640px;height:370px;background:linear-gradient(180deg,#e9ecef 0%,#d5d9dd 100%)}
.video-screen{position:absolute;left:116px;top:4px;width:430px;height:335px;border-radius:16px;background:#151515}
.video-image{position:absolute;left:36px;top:30px;width:358px;height:272px;background:linear-gradient(180deg,#b9cfe3 0%,#c9c2aa 55%,#8a8f93 100%)}
.play{position:absolute;left:50%;top:50%;transform:translate(-50%,-50%)}

/* Contact strip */
.contact-strip{height:43px;background:var(--orange);position:relative;color:var(--white);font-family:'Montserrat',sans-serif;font-weight:600;font-size:21px;white-space:nowrap}
.strip-item{position:absolute;top:0;height:43px;display:flex;align-items:center;gap:14px}
.strip-icon{width:38px;height:43px;background:var(--orange-dark);display:flex;align-items:center;justify-content:center}
.strip-call{left:266px}
.strip-mail{left:586px}

/* Our work */
.work{height:395px;background:var(--white);padding-top:32px;position:relative}
.work .divider-dots{background:var(--white)}
.work-grid{position:absolute;left:81px;top:131px;display:flex;gap:3px}
.work-card{position:relative;width:344px;height:220px}
.work-card:nth-child(1){background:linear-gradient(180deg,#a9b6c2 0%,#7f8f86 60%,#5e6b57 100%)}
.work-card:nth-child(2){background:linear-gradient(180deg,#9cc6e6 0%,#a86c55 55%,#4f7a3f 100%)}
.work-card:nth-child(3){background:linear-gradient(180deg,#d8d8d2 0%,#b9b8ad 55%,#3f6f33 100%)}
.work-card .play{top:45%}
.work-caption{position:absolute;left:0;right:0;bottom:0;height:34px;background:rgba(20,20,20,.72);color:var(--white);font-size:13px;font-weight:700;text-align:center;line-height:34px}
.carousel-arrow{position:absolute;top:232px}
.carousel-prev{left:38px}
.carousel-next{left:1139px}

/* Why us */
.why{height:380px;background:var(--bg-why);padding-top:36px;position:relative}
.why .divider-dots{background:var(--bg-why)}
.why-grid{position:absolute;left:43px;top:143px;width:1114px;display:flex}
.why-item{flex:1;text-align:center;position:relative}
.why-item + .why-item::before{content:"";position:absolute;left:0;top:54px;height:141px;width:1px;background:#dedede}
.why-icon{height:88px;display:flex;align-items:center;justify-content:center}
.why-title{font-family:'Montserrat',sans-serif;font-weight:600;font-size:23px;color:var(--ink);margin-top:18px;white-space:nowrap}
.why-item.is-accent .why-title{color:var(--orange)}
.why-text{font-size:15px;line-height:20px;color:var(--ink);margin-top:9px}
.why-text .more{font-weight:700}
.why-item.is-accent .more{color:var(--orange)}

/* Contact */
.contact{height:381px;background:var(--bg-contact);padding-top:30px;position:relative}
.contact .divider-dots{background:var(--bg-contact)}
.contact-intro{text-align:center;font-size:16px;color:var(--ink);margin-top:36px}
.contact-form{position:absolute;left:349px;top:169px;width:499px}
.form-cols{display:flex;justify-content:space-between}
.form-col{width:238px;display:flex;flex-direction:column;gap:9px}
.field{height:26px;background:var(--white);border:1px solid #dcdcdc;font-size:11px;font-style:italic;color:var(--muted);padding:5px 10px}
.field-message{height:61px}
.submit{margin-top:14px;height:50px;background:var(--orange);color:var(--white);font-family:'Montserrat',sans-serif;font-weight:600;font-size:22px;text-align:center;line-height:50px;border-radius:2px;letter-spacing:.5px}

/* Footer */
.site-footer{height:45px;background:var(--footer);color:#e8e8e8;font-size:14px;text-align:center;line-height:45px}
</style>
</head>
<body>

<header class="site-header">
  <div class="brand"><span class="brand-dot"></span><span class="brand-name">SkyLoftReels</span></div>
  <div class="header-phone">
    <svg viewBox="0 0 28 28"><circle cx="14" cy="14" r="12.5" fill="none" stroke="#f15a29" stroke-width="2"/><path d="M10 8.5c1-.6 1.8-.2 2.3.8l.8 1.7c.3.7 0 1.3-.6 1.7l-.7.5c.6 1.6 1.6 2.7 3.1 3.4l.6-.7c.5-.6 1.1-.7 1.7-.3l1.6 1c.9.6 1 1.4.3 2.2-1.3 1.5-3 1.6-5 .4-2.6-1.6-4.3-3.9-5-6.5-.4-1.8.1-3.3.9-4.2z" fill="#f15a29"/></svg>
    <span>123 456 7890</span>
  </div>
  <nav class="main-nav">
    <a href="#" class="is-active">HOME</a>
    <a href="#">ABOUT US</a>
    <a href="#">SERVCIES</a>
    <a href="#">PORTFOLIO</a>
    <a href="#">CONTACT US</a>
  </nav>
</header>

<section class="hero" role="img" aria-label="Aerial drone photo of suburban family homes among green trees under a blue sky">
  <div class="hero-banner">
    <h1 class="hero-title">SKYLOFTREELS</h1>
    <p class="hero-sub">We Film Your Home To Increase Your Chances of Sale</p>
  </div>
</section>

<section class="how">
  <h2 class="section-title"><span class="accent">HOW DOES</span> IT WORK?</h2>
  <div class="divider"><div class="divider-dots"><span></span><span></span><span></span></div></div>
  <div class="video-frame" role="img" aria-label="Hands holding a tablet playing an explainer video of a drone pilot filming a house">
    <div class="video-screen">
      <div class="video-image"></div>
      <svg class="play" width="80" height="80" viewBox="0 0 80 80"><circle cx="40" cy="40" r="37" fill="#ffffff" stroke="#f15a29" stroke-width="3"/><circle cx="40" cy="40" r="32" fill="#f15a29"/><path d="M32 25l22 15-22 15z" fill="#ffffff"/></svg>
    </div>
  </div>
</section>

<div class="contact-strip">
  <div class="strip-item strip-call">
    <span class="strip-icon"><svg width="24" height="24" viewBox="0 0 28 28"><circle cx="14" cy="14" r="12" fill="none" stroke="#fff" stroke-width="2"/><path d="M10 8.5c1-.6 1.8-.2 2.3.8l.8 1.7c.3.7 0 1.3-.6 1.7l-.7.5c.6 1.6 1.6 2.7 3.1 3.4l.6-.7c.5-.6 1.1-.7 1.7-.3l1.6 1c.9.6 1 1.4.3 2.2-1.3 1.5-3 1.6-5 .4-2.6-1.6-4.3-3.9-5-6.5-.4-1.8.1-3.3.9-4.2z" fill="#fff"/></svg></span>
    <span>Call Us - 31 647208351</span>
  </div>
  <div class="strip-item strip-mail">
    <span class="strip-icon"><svg width="24" height="18" viewBox="0 0 24 18"><rect x="1" y="1" width="22" height="16" fill="#fff"/><path d="M1 1l11 9 11-9" fill="none" stroke="#c9441b" stroke-width="2"/></svg></span>
    <span>Mail Us - lucas@skyloftreels.example</span>
  </div>
</div>

<section class="work">
  <h2 class="section-title"><span class="accent">OUR</span> WORK</h2>
  <div class="divider"><div class="divider-dots"><span></span><span></span><span></span></div></div>
  <svg class="carousel-arrow carousel-prev" width="18" height="30" viewBox="0 0 18 30"><path d="M15 3L4 15l11 12" fill="none" stroke="#c9c9c9" stroke-width="3"/></svg>
  <div class="work-grid">
    <article class="work-card" role="img" aria-label="Drone hovering over a misty valley">
      <svg class="play" width="50" height="50" viewBox="0 0 50 50"><circle cx="25" cy="25" r="23" fill="#fff" stroke="#f15a29" stroke-width="2"/><path d="M19 14l17 11-17 11z" fill="#111"/></svg>
      <div class="work-caption">Loren Ipsum Dolor Sit</div>
    </article>
    <article class="work-card" role="img" aria-label="Drone filming brick townhouses on a sunny day">
      <svg class="play" width="50" height="50" viewBox="0 0 50 50"><circle cx="25" cy="25" r="23" fill="#fff" stroke="#f15a29" stroke-width="2"/><path d="M19 14l17 11-17 11z" fill="#111"/></svg>
      <div class="work-caption">Loren Ipsum Dolor Sit</div>
    </article>
    <article class="work-card" role="img" aria-label="Drone hovering in front of a white house entrance">
      <svg class="play" width="50" height="50" viewBox="0 0 50 50"><circle cx="25" cy="25" r="23" fill="#fff" stroke="#f15a29" stroke-width="2"/><path d="M19 14l17 11-17 11z" fill="#111"/></svg>
      <div class="work-caption">Loren Ipsum Dolor Sit</div>
    </article>
  </div>
  <svg class="carousel-arrow carousel-next" width="18" height="30" viewBox="0 0 18 30"><path d="M3 3l11 12L3 27" fill="none" stroke="#c9c9c9" stroke-width="3"/></svg>
</section>

<section class="why">
  <h2 class="section-title"><span class="accent">WHY</span> US?</h2>
  <div class="divider"><div class="divider-dots"><span></span><span></span><span></span></div></div>
  <div class="why-grid">
    <div class="why-item is-accent">
      <div class="why-icon"><svg width="88" height="88" viewBox="0 0 88 88" role="img" aria-label="Savings icon"><circle cx="44" cy="50" r="34" fill="#f15a29"/><circle cx="48" cy="14" r="12" fill="#f15a29"/></svg></div>
      <h3 class="why-title">Cheap</h3>
      <p class="why-text">Lorem ipsum dolor sit amet,<br>consectetuer adipis <span class="more">...[+]</span></p>
    </div>
    <div class="why-item">
      <div class="why-icon"><svg width="84" height="84" viewBox="0 0 84 84"><path d="M42 12a30 30 0 0 0-28 40" fill="none" stroke="#111" stroke-width="12"/><path d="M4 44l10 16 14-12z" fill="#111"/><path d="M42 72a30 30 0 0 0 28-40" fill="none" stroke="#111" stroke-width="12"/><path d="M80 40L70 24 56 36z" fill="#111"/></svg></div>
      <h3 class="why-title">Flexible</h3>
      <p class="why-text">Lorem ipsum dolor sit amet,<br>consectetuer adipis <span class="more">...[+]</span></p>
    </div>
    <div class="why-item">
      <div class="why-icon"><svg width="88" height="88" viewBox="0 0 88 88"><polygon points="44,2 54,14 70,10 72,26 86,34 78,48 86,62 70,68 68,84 54,78 44,88 34,78 18,82 16,66 2,58 10,44 2,30 18,24 20,8 34,12" fill="#111"/><path d="M30 44h8v18h-8zM40 60V44l8-12c3 0 4 2 3 6l-2 6h10c3 0 4 3 2 5l-3 8c-1 2-2 3-4 3z" fill="#fff"/></svg></div>
      <h3 class="why-title">Quality</h3>
      <p class="why-text">Lorem ipsum dolor sit amet,<br>consectetuer adipis <span class="more">...[+]</span></p>
    </div>
    <div class="why-item">
      <div class="why-icon"><svg width="90" height="90" viewBox="0 0 90 90"><rect x="30" y="56" width="10" height="18" fill="#111"/><rect x="44" y="44" width="10" height="30" fill="#111"/><rect x="58" y="32" width="10" height="42" fill="#111"/><path d="M14 60l28-26 10 8 24-22" fill="none" stroke="#111" stroke-width="6"/><path d="M68 12h18v18z" fill="#111"/><path d="M6 80h74" stroke="#111" stroke-width="6"/><text x="14" y="30" font-family="Montserrat,sans-serif" font-weight="700" font-size="22" fill="#111">$</text></svg></div>
      <h3 class="why-title">Increase Sale Chance</h3>
      <p class="why-text">Lorem ipsum dolor sit amet,<br>consectetuer adipis <span class="more">...[+]</span></p>
    </div>
  </div>
</section>

<section class="contact">
  <h2 class="section-title"><span class="accent">CONTACT</span> US</h2>
  <div class="divider"><div class="divider-dots"><span></span><span></span><span></span></div></div>
  <p class="contact-intro">Fill In The Form Below And We Will Get Back To You Within 48 Hours.</p>
  <form class="contact-form">
    <div class="form-cols">
      <div class="form-col">
        <div class="field">First Name</div>
        <div class="field">Last Name</div>
        <div class="field">Phone Number</div>
      </div>
      <div class="form-col">
        <div class="field">Email</div>
        <div class="field field-message">Message</div>
      </div>
    </div>
    <div class="submit">SUBMIT</div>
  </form>
</section>

<footer class="site-footer">Copyright © 2016 SkyLoftReels . All Right Reserved.</footer>

</body>
</html>
```